Business Card Design

I already have a company logo for my company. I have a logo for the manufacturer we represent. I want a professional business card design.

```html
<!DOCTYPE html>
<html lang="en">
<head>
<meta charset="utf-8">
<title>Beacon Alert Group — Business Card</title>
<link href="https://fonts.googleapis.com/css2?family=Poppins:wght@400;600;700&display=swap" rel="stylesheet">
<style>
  :root {
    --stage: #222222;
    --card-black: #0d0d0d;
    --brand-red: #e31e25;
    --brand-gold: #c9960f;
    --ink-white: #ffffff;
  }
  * { box-sizing: border-box; margin: 0; padding: 0; }
  html, body {
    width: 1200px; height: 1015px; overflow: hidden;
    background: var(--stage);
    font-family: "Poppins", sans-serif;
  }
  .stage {
    width: 1200px; height: 1015px;
    display: flex; flex-direction: column;
    align-items: center; justify-content: center; gap: 40px;
  }
  .card {
    position: relative;
    width: 760px; height: 434px;
    overflow: hidden;
    box-shadow: 0 14px 30px rgba(0,0,0,.45);
  }
  .card-front {
    background: var(--card-black);
    display: flex; align-items: center; justify-content: center;
  }
  .brand {
    display: flex; align-items: center; gap: 16px;
    color: var(--brand-red);
    font-weight: 700;
    text-transform: uppercase;
    letter-spacing: 1px;
  }
  .brand-dot {
    flex: none;
    border-radius: 50%;
    background: var(--brand-red);
  }
  .card-front .brand { font-size: 40px; }
  .card-front .brand-dot { width: 34px; height: 34px; }

  .card-back { background: var(--brand-red); }
  .card-back .art {
    position: absolute; inset: 0; width: 760px; height: 434px;
  }
  .card-back .brand {
    position: absolute; left: 455px; top: 135px;
    font-size: 24px; gap: 10px;
    flex-direction: column; align-items: flex-start;
    line-height: 1.1;
  }
  .card-back .brand-dot { width: 22px; height: 22px; }

  .contact {
    position: absolute; left: 58px; top: 92px;
    color: var(--ink-white);
  }
  .person-name { font-size: 27px; font-weight: 700; letter-spacing: .5px; line-height: 1.1; }
  .person-role { font-size: 19px; font-weight: 400; margin-top: 2px; }
  .address {
    margin-top: 78px;
    font-size: 18px; line-height: 1.35;
    font-style: normal;
  }
  .lines { list-style: none; margin-top: 22px; font-size: 18px; line-height: 1.4; }
  .lines li { display: flex; align-items: center; gap: 10px; }
  .lines svg { width: 18px; height: 18px; flex: none; }
</style>
</head>
<body>
<main class="stage">

  <section class="card card-front" aria-label="Card front">
    <div class="brand"><span class="brand-dot"></span><span>Beacon Alert Group</span></div>
  </section>

  <section class="card card-back" aria-label="Card back">
    <svg class="art" viewBox="0 0 760 434" aria-hidden="true">
      <circle cx="575" cy="130" r="258" fill="var(--card-black)"/>
      <circle cx="600" cy="118" r="246" fill="var(--brand-gold)"/>
      <circle cx="612" cy="112" r="240" fill="var(--card-black)"/>
    </svg>

    <div class="brand"><span class="brand-dot"></span><span>Beacon Alert<br>Group</span></div>

    <div class="contact">
      <h1 class="person-name">DANIEL CARTER</h1>
      <p class="person-role">Managing Director</p>
      <address class="address">87, Harbor Road<br>Riverton, 30418</address>
      <ul class="lines">
        <li>
          <svg viewBox="0 0 24 24" fill="var(--ink-white)"><path d="M6.6 10.8a15 15 0 0 0 6.6 6.6l2.2-2.2a1 1 0 0 1 1-.25 11.4 11.4 0 0 0 3.6.6 1 1 0 0 1 1 1V20a1 1 0 0 1-1 1A17 17 0 0 1 3 4a1 1 0 0 1 1-1h3.5a1 1 0 0 1 1 1c0 1.25.2 2.45.6 3.6a1 1 0 0 1-.25 1z"/></svg>
          <span>044-555 018 274</span>
        </li>
        <li>
          <svg viewBox="0 0 24 24" fill="none" stroke="var(--ink-white)" stroke-width="2"><rect x="3" y="5" width="18" height="14"/><path d="M3 6l9 7 9-7"/></svg>
          <span>hello@beaconalert.com</span>
        </li>
        <li>
          <svg viewBox="0 0 24 24" fill="none" stroke="var(--ink-white)" stroke-width="1.8"><circle cx="12" cy="12" r="9"/><path d="M3 12h18M12 3c3 3 3 15 0 18M12 3c-3 3-3 15 0 18"/></svg>
          <span>www.beaconalert.com</span>
        </li>
      </ul>
    </div>
  </section>

</main>
</body>
</html>
```